Creative Web Design for an ERP (technology) Consulting Business

I need two pages designed for the ERP Project Management Consulting Company I am starting. One page is the home page, the other page is an important inside page.

I've looked at many different templates for sites like this, and they all look the same to me. I am working with PixelGuild designers because I want something unique.

This site will be implemented with Wordpress using the Elementor framework,

About Me ---
I have worked with PixelGuild several times before, and I have tired to do everything I can to ve helpful. In the uploads, you will find PDF's with wireframes outlning the layout of the pages, as well as explanatios for each section. There are Word documents that you can copy into text. The list below explains the files included.

Although the wireframes suggest a layout, please feel free to use your creativity - often, I find that the designs I like the most are designs I have never thought of.

About the Company --
ERP (Enterprise Resource Planning) systems are business computer systems that tie different businesss functions together. These systems are expensive and complicated, and efforts to implement them often fail. The purpose of the company is to increase the chance of success by focusing on the things that need to be right.

I have uploaded several files to help clarify what I am looking for:
• 1a - Home Page Wireframe - PDF
Wireframe for the home page with an explanation of each section.
• 1b - Home Page Text – Word
A Word document so that you can copy the text.
• 2 - Copper Harbor Logo – ZIP
Four different versions of the company logo in Adobe Illustrator, PNG, and JPG formats. Any of the four are acceptable:
1. Logo_1 – Black on Transparent – Same Line ERP
2. Logo_2 – White on Transparent – Same Line ERP
3. Logo_3 – Black on Transparent – Big ERP on Different Line
4. Logo_4 – White on Transparent – Big ERP on Different Line
• 3a - Copper Harbor Page Wireframe – PDF
Wireframe for he Copper Harbor page, with explanations and a detailed breakdown of the top section.
• 3b - Copper Harbor Text – Word
• 4 - Colors and Palettes – PDF
• 5 - Change Management Icon – EPS
• 6 – Site Map
If you wish to see it, the site map provides an idea of the entire site. The two pages circled in red are the ones I need to be designed.

Thank you for your interest in this project!

Target Market(s)

Corporate decision makers, primarily CIOs and CFOs, as well as ERP project managers and influencers.

Industry/Entity Type

Consulting

Number of Pages Required

2 page

Font styles to use
Sans Serif

Requirements
Must have
• Pages that contain the elements explained on the wireframes provided.
Nice to have
• A design that looks and feels unique
Should not have
• A typical, template layour

```html
<!DOCTYPE html>
<html lang="en">
<head>
<meta charset="utf-8">
<title>Copper Harbor Framework for ERP Success</title>
<link href="https://fonts.googleapis.com/css2?family=Inter:wght@400;500;600;700;800&display=swap" rel="stylesheet">
<style>
  :root{
    --ink:#111111;
    --muted:#6f7079;
    --page:#f4f4f6;
    --rule:#e2e2e6;
    --band:#cdd3dc;
    --band-card:#d7dbe2;
    --red:#d9594f;
    --orange:#e0814c;
    --gold:#d9a443;
    --green:#5f8f5e;
    --teal:#4e7186;
    --blue:#5670a8;
    --violet:#5a4a8a;
    --plum:#6a4f8e;
    --h-red:#c9473f;
    --h-gold:#c98a2a;
    --h-green:#4f7f52;
    --h-teal:#3f6a80;
    --h-blue:#3f5690;
    --h-violet:#5b4488;
  }
  *{box-sizing:border-box;margin:0;padding:0}
  html,body{width:673px;height:1200px;overflow:hidden}
  body{font-family:"Inter",Arial,sans-serif;background:var(--page);color:var(--ink);position:relative}
  .site-header{position:absolute;left:0;top:0;width:673px;height:53px;border-bottom:1px solid var(--rule)}
  .brand{position:absolute;left:23px;top:16px;font-size:17px;font-weight:700;letter-spacing:-.3px}
  .main-nav{position:absolute;left:218px;top:21px;display:flex;gap:24px;font-size:8.5px;font-weight:600;letter-spacing:.4px}
  .header-cta{position:absolute;left:548px;top:11px;width:106px;height:31px;border-radius:16px;background:var(--ink);color:#fff;font-size:9px;font-weight:600;display:flex;align-items:center;justify-content:center}
  .page-title{position:absolute;left:0;top:86px;width:673px;text-align:center;font-size:38px;line-height:44px;font-weight:700;letter-spacing:-.8px}
  .page-lede{position:absolute;left:120px;top:186px;width:433px;text-align:center;font-size:12.5px;line-height:20px;color:var(--muted)}
  .pillar-map{position:absolute;left:0;top:240px}
  .pillar{position:absolute;width:160px}
  .pillar h3{font-size:12.5px;line-height:16px;font-weight:600;margin-bottom:10px}
  .pillar p{font-size:7.6px;line-height:11.5px;color:#4a4a52}
  .summary-card{position:absolute;left:57px;top:930px;width:559px;height:80px;border-radius:20px 20px 0 0;background:var(--band-card)}
  .summary-band{position:absolute;left:0;top:993px;width:673px;height:207px;background:var(--band)}
  .summary-title{position:absolute;left:0;top:957px;width:673px;text-align:center;font-size:14.5px;line-height:19px;font-weight:600}
  .summary-note{position:absolute;left:0;top:997px;width:673px;text-align:center;font-size:11.5px;color:var(--muted)}
  .features{position:absolute;left:96px;top:1038px;width:500px;display:flex}
  .feature{width:168px;padding-left:8px;display:grid;grid-template-columns:20px 1fr;column-gap:9px;height:60px}
  .feature+.feature{border-left:1px solid #b9c0ca;padding-left:14px}
  .feature-dot{width:19px;height:19px;border-radius:50%;display:flex;align-items:center;justify-content:center}
  .feature h4{font-size:8px;font-weight:700;letter-spacing:.2px;margin-top:4px}
  .feature p{grid-column:2;font-size:8.3px;line-height:12.5px;color:#444;margin-top:4px}
  .learn-more{position:absolute;left:272px;top:1131px;width:130px;height:42px;border-radius:21px;background:var(--ink);color:#fff;font-size:11.5px;font-weight:600;display:flex;align-items:center;justify-content:center}
</style>
</head>
<body>
  <header class="site-header">
    <div class="brand">copperharbor</div>
    <nav class="main-nav"><span>ABOUT</span><span>PILLARS</span><span>SERVICES</span><span>BLOG</span><span>CONTACT</span></nav>
    <div class="header-cta">Let's Talk</div>
  </header>

  <h1 class="page-title">Copper Harbor Framework<br>for ERP success</h1>
  <p class="page-lede">What sets this eight pillar framework apart is how it frames your unique project and directs attention to what matters most.</p>

  <svg class="pillar-map" width="673" height="670" viewBox="0 240 673 670" aria-label="Eight pillar wheel diagram">
    <defs>
      <clipPath id="petal-outline">
        <path d="M0 318 Q0 296 30 296 L205 296 Q205 272 230 268 L318 264 Q330 258 336 246 Q342 258 354 264 L443 268 Q467 272 467 296 L643 296 Q673 296 673 318 L673 845 Q673 870 643 870 L467 870 Q467 880 443 882 L354 884 Q342 890 336 900 Q330 890 318 884 L230 882 Q205 880 205 870 L30 870 Q0 870 0 845 Z"/>
      </clipPath>
    </defs>
    <g clip-path="url(#petal-outline)">
      <path d="M336 582 L-30 -241 L702 -241 Z" fill="#f2cdbf"/>
      <path d="M336 582 L702 -241 L1165 230 Z" fill="#f1dcb6"/>
      <path d="M336 582 L1165 230 L1165 934 Z" fill="#dfe4cd"/>
      <path d="M336 582 L1165 934 L702 1405 Z" fill="#c9dde3"/>
      <path d="M336 582 L702 1405 L-30 1405 Z" fill="#c8d0e8"/>
      <path d="M336 582 L-30 1405 L-493 934 Z" fill="#d6cce6"/>
      <path d="M336 582 L-493 934 L-493 230 Z" fill="#dcd0e4"/>
      <path d="M336 582 L-493 230 L-30 -241 Z" fill="#f3cfc6"/>
    </g>
    <g stroke="#ffffff" stroke-width="1.3">
      <line x1="336" y1="582" x2="215" y2="306"/>
      <line x1="336" y1="582" x2="457" y2="306"/>
      <line x1="336" y1="582" x2="30" y2="452"/>
      <line x1="336" y1="582" x2="642" y2="452"/>
      <line x1="336" y1="582" x2="30" y2="712"/>
      <line x1="336" y1="582" x2="642" y2="712"/>
      <line x1="336" y1="582" x2="215" y2="856"/>
      <line x1="336" y1="582" x2="457" y2="856"/>
    </g>
    <g fill="#ffffff">
      <circle cx="215" cy="306" r="4"/><circle cx="457" cy="306" r="4"/>
      <circle cx="30" cy="452" r="4"/><circle cx="642" cy="452" r="4"/>
      <circle cx="30" cy="712" r="4"/><circle cx="642" cy="712" r="4"/>
      <circle cx="215" cy="856" r="4"/><circle cx="457" cy="856" r="4"/>
    </g>
    <g class="wheel" stroke="#ffffff" stroke-width="1.5">
      <path d="M336 582 L271 436 A160 160 0 0 1 401 436 Z" fill="var(--orange)"/>
      <path d="M336 582 L401 436 A160 160 0 0 1 483 519 Z" fill="var(--gold)"/>
      <path d="M336 582 L483 519 A160 160 0 0 1 483 645 Z" fill="var(--green)"/>
      <path d="M336 582 L483 645 A160 160 0 0 1 401 728 Z" fill="var(--teal)"/>
      <path d="M336 582 L401 728 A160 160 0 0 1 271 728 Z" fill="var(--blue)"/>
      <path d="M336 582 L271 728 A160 160 0 0 1 189 645 Z" fill="var(--violet)"/>
      <path d="M336 582 L189 645 A160 160 0 0 1 189 519 Z" fill="var(--plum)"/>
      <path d="M336 582 L189 519 A160 160 0 0 1 271 436 Z" fill="var(--red)"/>
    </g>
    <circle cx="336" cy="582" r="64" fill="#e4e6e0"/>
    <g fill="none" stroke="#4d6aa8" stroke-width="2">
      <rect x="313" y="558" width="30" height="44" rx="3"/>
      <line x1="319" y1="570" x2="337" y2="570"/><line x1="319" y1="580" x2="337" y2="580"/><line x1="319" y1="590" x2="331" y2="590"/>
      <rect x="340" y="570" width="20" height="24" rx="3"/>
      <line x1="350" y1="576" x2="350" y2="588"/><line x1="344" y1="582" x2="356" y2="582"/>
    </g>
    <g fill="none" stroke="#ffffff" stroke-width="1.4" stroke-linecap="round">
      <rect x="325" y="458" width="22" height="24" rx="2"/><line x1="330" y1="466" x2="342" y2="466"/><line x1="330" y1="472" x2="342" y2="472"/><line x1="330" y1="477" x2="338" y2="477"/>
      <path d="M406 514 L416 494 L426 514 M410 506 L422 506"/>
      <rect x="436" y="572" width="24" height="17" rx="2"/><line x1="442" y1="581" x2="454" y2="581"/><line x1="444" y1="593" x2="452" y2="593"/>
      <path d="M404 652 L416 656 L428 652 L424 668 L408 668 Z"/>
      <path d="M326 704 L326 684 L336 684 L336 696 L348 696 L348 704 Z"/>
      <rect x="245" y="652" width="10" height="10" rx="2"/><rect x="259" y="662" width="10" height="8" rx="2"/><line x1="250" y1="662" x2="250" y2="670"/>
      <circle cx="224" cy="582" r="8"/><circle cx="212" cy="572" r="2"/><circle cx="236" cy="572" r="2"/><circle cx="224" cy="596" r="2"/>
      <circle cx="252" cy="500" r="6"/><path d="M244 514 Q252 506 262 512 L266 504"/>
    </g>
  </svg>

  <section class="pillars">
    <div class="pillar" style="left:274px;top:285px;width:140px"><h3 style="color:var(--h-red)">Align with the right<br>project approach.</h3><p>Select a delivery model that suits<br>the scope of your project and the<br>way your people already work and<br>support decisions.</p></div>
    <div class="pillar" style="left:27px;top:345px"><h3 style="color:var(--h-red)">Executive support<br>and clear goals.</h3><p>Leaders set a shared direction early<br>so every team knows what matters<br>and can make choices that stay<br>on track.</p></div>
    <div class="pillar" style="left:491px;top:345px"><h3 style="color:var(--h-gold)">Disciplined business<br>process design</h3><p>Map current and future processes<br>before configuring anything so<br>the system serves the way you<br>really operate.</p></div>
    <div class="pillar" style="left:27px;top:532px"><h3 style="color:var(--h-violet)">Build the Needly<br>team and skills</h3><p>Staff the project with people who<br>know the business and give them<br>the time, training and authority<br>to make real progress on every<br>core task.</p></div>
    <div class="pillar" style="left:512px;top:532px"><h3 style="color:var(--h-green)">Manage risks with<br>clear reports</h3><p>Track progress and risks openly<br>so issues surface early and are<br>handled before they grow into<br>costly delays.</p></div>
    <div class="pillar" style="left:27px;top:722px"><h3 style="color:var(--h-violet)">Change planning<br>for adoption</h3><p>Help people understand why the<br>system is changing and how their<br>daily work will benefit so the<br>new tools are used with<br>confidence.</p></div>
    <div class="pillar" style="left:492px;top:722px"><h3 style="color:var(--h-teal)">Data quality<br>and governance</h3><p>Clean, owned and trusted data<br>keeps reports useful and gives<br>your team a sound base for<br>each decision.</p></div>
    <div class="pillar" style="left:275px;top:768px;width:140px"><h3 style="color:var(--h-blue)">Partner with<br>vendors wisely</h3><p>Choose partners who share your<br>goals, define their roles and<br>hold them to clear results.<br>Open, steady dialogue keeps<br>all sides aligned.</p></div>
  </section>

  <div class="summary-card"></div>
  <div class="summary-band"></div>
  <h2 class="summary-title">The adaptive approach of the framework combines<br>the iterative approach to planning with Agile execution.</h2>
  <p class="summary-note">All stages share the same list of core practices.</p>

  <div class="features">
    <div class="feature"><span class="feature-dot" style="background:#8a74b4"><svg width="9" height="9" viewBox="0 0 9 9" fill="none" stroke="#fff"><rect x="1" y="1" width="7" height="7" rx="1"/></svg></span><h4>ADAPTIVE GUIDES</h4><p>Essential planning for<br>Practical Projects</p></div>
    <div class="feature"><span class="feature-dot" style="background:#9a9ea8"><svg width="9" height="9" viewBox="0 0 9 9" fill="none" stroke="#fff"><circle cx="4.5" cy="4.5" r="3"/></svg></span><h4>ITERATIVE STEPS</h4><p>Focused sprints to<br>Practical Releases</p></div>
    <div class="feature"><span class="feature-dot" style="background:#8a74b4"><svg width="9" height="9" viewBox="0 0 9 9" fill="none" stroke="#fff"><path d="M2 7 L4.5 2 L7 7"/></svg></span><h4>AGILE ROLES</h4><p>Shared ownership for<br>Every Stage</p></div>
  </div>

  <div class="learn-more">Learn More</div>
</body>
</html>
```